A clean crisp business card for a Landscape Construction company. Designed to be easy to read contact/ info and also be appealing/interesting, unlike a traditional business card.

Industry/Entity Type

Landscape Construction

Contact Information for Business Card

Company name : Brambleford Landscape Construction, phone number: (877) 62Vista, website:Bramblefordyards.example, Email, sales@bramblefordyards.example

Requirements
Nice to have
• Luxurious finishes/ details…. Icons or emblems next to contact info
Should not have
• Clipart or general pictures

```html
<!DOCTYPE html>
<html lang="en">
<head>
<meta charset="utf-8">
<title>Brambleford Landscape Construction – Business Card</title>
<link href="https://fonts.googleapis.com/css2?family=Arimo:wght@400;700&family=Tinos:wght@700&display=swap" rel="stylesheet">
<style>
  :root {
    --page-bg: #1b1b1c;
    --card-bg: #2a2a2b;
    --brand-blue: #1f6fc4;
    --brand-green: #8cc63f;
    --text-light: #f2f2f2;
  }
  * { margin: 0; padding: 0; box-sizing: border-box; }
  html, body {
    width: 1200px; height: 900px; overflow: hidden;
    background: var(--page-bg);
  }
  .stage {
    width: 1200px; height: 900px;
    display: flex; align-items: center; justify-content: center;
  }
  .card {
    position: relative;
    width: 1050px; height: 600px;
    background: var(--card-bg);
    border-radius: 34px;
    box-shadow: 0 24px 60px rgba(0,0,0,0.55);
    color: var(--text-light);
    font-family: "Arimo", Arial, sans-serif;
  }
  .holder {
    position: absolute; left: 70px; top: 58px;
    display: flex; align-items: flex-start; gap: 16px;
  }
  .holder__bar {
    width: 22px; height: 62px;
    background: var(--brand-blue);
  }
  .holder__name {
    font-family: "Tinos", "Times New Roman", serif;
    font-weight: 700;
    font-size: 42px;
    letter-spacing: 1px;
    line-height: 1;
  }
  .holder__first { color: var(--brand-blue); }
  .holder__last { color: var(--brand-green); }
  .holder__title {
    font-size: 24px; margin-top: 8px; color: var(--text-light);
  }
  .address {
    position: absolute; left: 158px; top: 190px;
    font-size: 27px; line-height: 1.3; font-style: normal;
  }
  .contact {
    position: absolute; left: 118px; top: 310px;
    list-style: none;
    font-size: 27px; line-height: 1.45;
  }
  .contact__item { display: flex; align-items: center; gap: 12px; }
  .contact__icon { width: 22px; height: 22px; flex: none; }
  .brand {
    position: absolute; right: 70px; bottom: 50px;
    display: flex; align-items: center; gap: 16px;
  }
  .brand__dot {
    width: 34px; height: 34px; border-radius: 50%;
    background: var(--brand-green);
  }
  .brand__name {
    font-family: "Arimo", Arial, sans-serif;
    font-weight: 700;
    font-size: 36px;
    line-height: 1.1;
    color: var(--brand-blue);
    text-align: right;
  }
</style>
</head>
<body>
<main class="stage">
  <article class="card">
    <header class="holder">
      <div class="holder__bar"></div>
      <div>
        <p class="holder__name"><span class="holder__first">OWEN</span> <span class="holder__last">HARTLEY</span></p>
        <p class="holder__title">Founder</p>
      </div>
    </header>

    <address class="address">
      214 Larchmont Road<br>
      Hollow Creek, AB 41620
    </address>

    <ul class="contact">
      <li class="contact__item">
        <svg class="contact__icon" viewBox="0 0 24 24" aria-hidden="true">
          <path fill="#8cc63f" d="M6.6 10.8a15 15 0 0 0 6.6 6.6l2.2-2.2a1 1 0 0 1 1-.25 11.4 11.4 0 0 0 3.6.57 1 1 0 0 1 1 1V20a1 1 0 0 1-1 1A17 17 0 0 1 3 4a1 1 0 0 1 1-1h3.5a1 1 0 0 1 1 1c0 1.25.2 2.450.57 3.57a1 1 0 0 1-.25 1z"/>
        </svg>
        <span>(877) 62Vista</span>
      </li>
      <li class="contact__item">
        <svg class="contact__icon" viewBox="0 0 24 24" aria-hidden="true">
          <rect x="2" y="5" width="20" height="14" rx="2" fill="#8cc63f"/>
          <path d="M3 6l9 7 9-7" fill="none" stroke="#2a2a2b" stroke-width="2"/>
        </svg>
        <span>sales@bramblefordyards.example</span>
      </li>
      <li class="contact__item">
        <svg class="contact__icon" viewBox="0 0 24 24" aria-hidden="true">
          <circle cx="12" cy="12" r="10" fill="#8cc63f"/>
          <path d="M2 12h20M12 2c3 3 3 17 0 20M12 2c-3 3-3 17 0 20" fill="none" stroke="#2a2a2b" stroke-width="1.6"/>
        </svg>
        <span>bramblefordyards.example</span>
      </li>
    </ul>

    <div class="brand">
      <span class="brand__dot"></span>
      <p class="brand__name">Brambleford<br>Landscape Construction</p>
    </div>
  </article>
</main>
</body>
</html>
```